Disposable Mini Sauce Pot Design for Asian Chain Food Brands

We operate a Hainan Chicken Rice takeout brand under the name Brindle4U, with our official website: www.Brindle4U.example.
We offer four signature house sauces and are launching brand-new packaging for our sauce line. We require custom graphic designs exclusively for the sauce cup lids.
Product Material & Base Specs
The sauce cups are made of PP plastic, available in two translucent base options: Translucent White and Translucent Orange.
Four Sauce Varieties for Individual Lid Designs
1. Red Sauce – Fried Sweet Chili Sauce
2.Green Sauce – Scallion Oil Dressing
3.Sweet Soy Sauce
4.Sweet Red Sauce (Special for Fried Chicken)
Differentiate each sauce lid design through unique graphics, typography, or illustrative elements for easy customer identification.
The marking NET WT 2 OZ must be clearly printed on every lid.
**There is no need to print full descriptive text or the full name of the sauces on each lid; the design only needs to clearly differentiate the four sauce varieties.
**Please reference the original design style and brand color palette shown on our official website, and feel free to fully unleash your creativity.
Look and feel
Each slider illustrates characteristics of the customer's brand and the style your logo design should communicate.

```html
<!DOCTYPE html>
<html lang="en">
<head>
<meta charset="utf-8">
<title>Brindle4U Sauce Lids</title>
<link rel="stylesheet" href="https://fonts.googleapis.com/css2?family=Montserrat:wght@800;900&display=swap">
<style>
  :root {
    --page: #fafafa;
    --ink: #ffffff;
    --splash: #ec7a22;
    --red: #c8161f;
    --red-deep: #b80f22;
    --green: #6cab2b;
    --green-deep: #62a027;
    --purple: #834487;
    --purple-deep: #7a3d80;
    --brick: #a71d0c;
    --brick-deep: #98180a;
  }
  * { box-sizing: border-box; margin: 0; padding: 0; }
  html, body { width: 1072px; height: 1200px; overflow: hidden; background: var(--page); }
  body { position: relative; font-family: "Montserrat", sans-serif; color: var(--ink); }

  .lid {
    position: absolute;
    width: 448px;
    height: 507px;
    border-radius: 78px;
    overflow: hidden;
  }
  .lid--red    { left: 78px;  top: 69px;  background: radial-gradient(circle at 50% 45%, var(--red) 0%, var(--red-deep) 100%); }
  .lid--green  { left: 549px; top: 69px;  background: radial-gradient(circle at 50% 45%, var(--green) 0%, var(--green-deep) 100%); }
  .lid--purple { left: 78px;  top: 620px; background: radial-gradient(circle at 50% 45%, var(--purple) 0%, var(--purple-deep) 100%); }
  .lid--brick  { left: 549px; top: 620px; background: radial-gradient(circle at 50% 45%, var(--brick) 0%, var(--brick-deep) 100%); }

  .splash {
    position: absolute;
    left: 60px;
    top: 110px;
    width: 340px;
    height: 260px;
    background: var(--splash);
    border-radius: 48% 52% 44% 56% / 55% 45% 58% 42%;
  }

  .title {
    position: absolute;
    left: 0;
    right: 0;
    text-align: center;
    font-weight: 900;
    line-height: 1;
    letter-spacing: -3px;
  }
  .title span { display: block; }
  .title .big-caps { font-size: 112px; height: 84px; line-height: 84px; }
  .title .big-caps--wide { font-size: 104px; letter-spacing: -4px; }
  .title .word { font-size: 128px; height: 76px; line-height: 58px; letter-spacing: -4px; }
  .title .small-caps { font-size: 60px; height: 48px; line-height: 48px; letter-spacing: -1px; }

  .lid--red .title, .lid--green .title { top: 148px; }
  .lid--purple .title, .lid--brick .title { top: 108px; }

  .descriptor {
    position: absolute;
    left: 37px;
    top: 404px;
    font-size: 18px;
    font-weight: 900;
    line-height: 18px;
    letter-spacing: 0;
    text-transform: uppercase;
  }
  .net-weight {
    position: absolute;
    left: 37px;
    top: 466px;
    font-size: 14px;
    font-weight: 900;
    letter-spacing: -0.2px;
  }
  .brand-name {
    position: absolute;
    right: 16px;
    top: 416px;
    font-size: 24px;
    font-weight: 900;
    letter-spacing: -0.5px;
  }
</style>
</head>
<body>

  <section class="lid lid--red">
    <div class="splash" role="img" aria-label="Orange sauce splash graphic"></div>
    <h2 class="title"><span class="big-caps">RED</span><span class="word">sauce</span></h2>
    <p class="descriptor">Fried Sweet<br>Chili Sauce</p>
    <p class="net-weight">NET WT 2 OZ</p>
    <p class="brand-name">Brindle4U</p>
  </section>

  <section class="lid lid--green">
    <div class="splash" role="img" aria-label="Orange sauce splash graphic"></div>
    <h2 class="title"><span class="big-caps big-caps--wide">GREEN</span><span class="word">sauce</span></h2>
    <p class="descriptor">Scallion Oil<br>Dressing</p>
    <p class="net-weight">NET WT 2 OZ</p>
    <p class="brand-name">Brindle4U</p>
  </section>

  <section class="lid lid--purple">
    <div class="splash" role="img" aria-label="Orange sauce splash graphic"></div>
    <h2 class="title"><span class="word">sweet</span><span class="small-caps">SOY</span><span class="word">sauce</span></h2>
    <p class="descriptor">Scallion Oil<br>Dressing</p>
    <p class="net-weight">NET WT 2 OZ</p>
    <p class="brand-name">Brindle4U</p>
  </section>

  <section class="lid lid--brick">
    <div class="splash" role="img" aria-label="Orange sauce splash graphic"></div>
    <h2 class="title"><span class="word">sweet</span><span class="big-caps">RED</span><span class="word">sauce</span></h2>
    <p class="descriptor">Special for<br>Fried Chicken</p>
    <p class="net-weight">NET WT 2 OZ</p>
    <p class="brand-name">Brindle4U</p>
  </section>

</body>
</html>
```